Business Card Design

New business card design

Target Market(s)

Residential & Commercial Property Managers

Industry/Entity Type

Plumbing Services

Contact Information for Business Card

Name - Rowan Keddle, title - Director, Phone Number - 0431 286 517, email - rowan@tbk-plumbing.com.au, Company ABN - 73 215 904 386,

Font styles to use
Sans Serif

Colors
0054AA
0677BA
7BADD7
CADEEF
E8F1F8

```html
<!DOCTYPE html>
<html lang="en">
<head>
<meta charset="utf-8">
<title>TBK Plumbing Services – Business Card</title>
<link href="https://fonts.googleapis.com/css2?family=Inter:wght@400;600;700&display=swap" rel="stylesheet">
<style>
  :root {
    --page-bg: #e9ecef;
    --card-white: #ffffff;
    --card-navy: #18202a;
    --ink-dark: #1a2530;
    --brand-blue: #2a9ad8;
    --text-light: #f2f5f8;
    --rule-blue: #245a7a;
    --shadow: rgba(20, 30, 40, 0.22);
  }
  * { box-sizing: border-box; margin: 0; padding: 0; }
  html, body {
    width: 1200px; height: 900px; overflow: hidden;
    background: var(--page-bg);
    font-family: "Inter", Arial, sans-serif;
  }
  .canvas {
    position: relative; width: 1200px; height: 900px;
    display: flex; flex-direction: column; align-items: center; justify-content: center; gap: 50px;
  }
  .card {
    position: relative; width: 630px; height: 360px;
    border-radius: 36px;
    box-shadow: 0 14px 30px var(--shadow);
    overflow: hidden;
  }
  /* Front */
  .card-front { background: linear-gradient(135deg, #f1f2f3 0%, var(--card-white) 60%); }
  .website {
    position: absolute; top: 40px; right: 44px;
    font-size: 17px; letter-spacing: 3px; color: var(--ink-dark);
  }
  .website .domain { color: var(--brand-blue); }
  .front-logo {
    position: absolute; left: 140px; top: 140px;
    display: flex; align-items: center; gap: 18px;
  }
  .logo-dot { width: 26px; height: 26px; border-radius: 50%; background: var(--brand-blue); flex: none; }
  .logo-text { color: var(--ink-dark); font-weight: 400; line-height: 1; }
  .logo-name { display: block; font-size: 96px; letter-spacing: 4px; }
  .logo-tag { display: block; font-size: 14px; letter-spacing: 9px; margin-top: 14px; padding-left: 4px; white-space: nowrap; }

  /* Back */
  .card-back { background: var(--card-navy); }
  .contact {
    position: absolute; left: 40px; top: 48px; width: 290px;
  }
  .contact-name { font-size: 26px; font-weight: 700; color: var(--brand-blue); letter-spacing: -0.5px; }
  .contact-title { font-size: 20px; color: var(--text-light); margin-top: 2px; }
  .contact-rule { height: 1px; background: var(--rule-blue); margin: 12px 0; width: 290px; }
  .contact-line {
    display: flex; align-items: center; gap: 10px;
    font-size: 17px; color: var(--text-light); margin-bottom: 8px; padding-left: 16px;
    white-space: nowrap;
  }
  .contact-line svg { width: 18px; height: 18px; flex: none; }
  .contact-abn { font-size: 22px; font-weight: 600; color: var(--text-light); padding-left: 32px; white-space: nowrap; }
  .contact-abn .abn-label { color: var(--brand-blue); }
  .back-logo {
    position: absolute; right: 40px; bottom: 34px;
    display: flex; align-items: center; gap: 14px;
  }
  .back-logo .logo-dot { width: 22px; height: 22px; }
  .back-logo .logo-text { color: var(--text-light); }
  .back-logo .logo-name { font-size: 72px; letter-spacing: 3px; }
  .back-logo .logo-tag { font-size: 11px; letter-spacing: 6px; margin-top: 12px; }
</style>
</head>
<body>
<main class="canvas">
  <section class="card card-front" aria-label="Business card front">
    <p class="website">www.<span class="domain">tbkplumbingservices</span>.com.au</p>
    <div class="front-logo">
      <span class="logo-dot" aria-hidden="true"></span>
      <p class="logo-text"><span class="logo-name">tbk</span><span class="logo-tag">plumbing services</span></p>
    </div>
  </section>

  <section class="card card-back" aria-label="Business card back">
    <div class="contact">
      <p class="contact-name">Rowan Keddle</p>
      <p class="contact-title">Director</p>
      <div class="contact-rule"></div>
      <p class="contact-line">
        <svg viewBox="0 0 24 24" aria-hidden="true"><path fill="#2a9ad8" d="M6.6 10.8a15.1 15.1 0 0 0 6.6 6.6l2.2-2.2a1 1 0 0 1 1-.25 11.4 11.4 0 0 0 3.6.57 1 1 0 0 1 1 1V20a1 1 0 0 1-1 1A17 17 0 0 1 3 4a1 1 0 0 1 1-1h3.5a1 1 0 0 1 1 1c0 1.25.2 2.45.57 3.57a1 1 0 0 1-.25 1z"/></svg>
        0431 286 517
      </p>
      <p class="contact-line">
        <svg viewBox="0 0 24 24" aria-hidden="true"><path fill="#2a9ad8" d="M3 5h18a1 1 0 0 1 1 1v12a1 1 0 0 1-1 1H3a1 1 0 0 1-1-1V6a1 1 0 0 1 1-1zm1 2.2V17h16V7.2l-8 5.3z"/></svg>
        rowan@tbk-plumbing.com.au
      </p>
      <div class="contact-rule"></div>
      <p class="contact-abn"><span class="abn-label">ABN - </span>73 215 904 386</p>
    </div>
    <div class="back-logo">
      <span class="logo-dot" aria-hidden="true"></span>
      <p class="logo-text"><span class="logo-name">tbk</span><span class="logo-tag">plumbing services</span></p>
    </div>
  </section>
</main>
</body>
</html>
```